Business Card Design

I already have a company logo for my company. I have a logo for the manufacturer we represent. I want a professional business card design.

```html
<!DOCTYPE html>
<html lang="en">
<head>
<meta charset="utf-8">
<title>Beacon Guard LLC – Business Card</title>
<link href="https://fonts.googleapis.com/css2?family=Lato:wght@400;700;900&display=swap" rel="stylesheet">
<style>
  :root{
    --page:#2b2c2e;
    --card-white:#ffffff;
    --card-black:#1c1c1e;
    --red:#e3202a;
    --amber:#e8a317;
    --ink:#3a3a3a;
    --grey-line:#d6d6d6;
    --icon:#1e1e1e;
  }
  *{box-sizing:border-box;margin:0;padding:0}
  html,body{width:1200px;height:952px;overflow:hidden}
  body{background:var(--page);font-family:'Lato',sans-serif;position:relative}

  .card{position:absolute;top:324px;width:530px;height:303px;border-radius:3px;overflow:hidden;box-shadow:0 14px 30px rgba(0,0,0,.45)}
  .card--front{left:50px;background:var(--card-white)}
  .card--back{left:620px;background:var(--card-black);display:flex;align-items:center;justify-content:center}

  .edge-line{position:absolute;left:28px;width:3px}
  .edge-line--grey{top:0;height:170px;background:var(--grey-line)}
  .edge-line--red{left:36px;top:176px;bottom:0;background:var(--red)}

  .brand{display:flex;align-items:center;gap:8px}
  .brand__square{width:16px;height:16px;background:var(--red);flex:none}
  .brand__name{font-weight:900;font-size:18px;letter-spacing:1px;color:var(--red);white-space:nowrap}
  .card--front .brand{position:absolute;left:56px;top:100px;width:224px}
  .card--back .brand__name{font-size:30px;letter-spacing:1.5px}
  .card--back .brand__square{width:24px;height:24px}
  .card--back .brand{gap:10px}

  .contact{position:absolute;left:300px;top:78px;width:220px}
  .contact__name{font-weight:900;font-size:17px;letter-spacing:.5px;color:var(--red)}
  .contact__title{font-size:12px;color:var(--ink);margin-top:2px}
  .contact__rule{width:36px;height:1.5px;background:var(--ink);margin:8px 0 12px}
  .contact__list{list-style:none}
  .contact__item{display:flex;align-items:flex-start;gap:8px;font-size:10.5px;color:var(--ink);line-height:1.35;margin-bottom:7px}
  .contact__icon{flex:none;width:15px;height:15px;border-radius:2px;background:var(--icon);display:flex;align-items:center;justify-content:center}
  .contact__icon--pin{background:var(--amber)}
  .contact__icon svg{width:10px;height:10px}
</style>
</head>
<body>

<section class="card card--front" aria-label="Business card front">
  <span class="edge-line edge-line--grey"></span>
  <span class="edge-line edge-line--red"></span>

  <div class="brand">
    <span class="brand__square"></span>
    <span class="brand__name">BEACON GUARD LLC</span>
  </div>

  <div class="contact">
    <h1 class="contact__name">DANIEL R. MARSH</h1>
    <p class="contact__title">Managing Director</p>
    <div class="contact__rule"></div>
    <ul class="contact__list">
      <li class="contact__item">
        <span class="contact__icon contact__icon--pin">
          <svg viewBox="0 0 10 10"><path d="M5 0.5a3.3 3.3 0 0 0-3.3 3.3C1.7 6.3 5 9.5 5 9.5s3.3-3.2 3.3-5.7A3.3 3.3 0 0 0 5 .5zm0 4.6a1.3 1.3 0 1 1 0-2.6 1.3 1.3 0 0 1 0 2.6z" fill="#fff"/></svg>
        </span>
        <span>217 Harbor Point Avenue<br>Baltimore, MD 21230</span>
      </li>
      <li class="contact__item">
        <span class="contact__icon">
          <svg viewBox="0 0 10 10"><path d="M2.2 1 3.8 2.8 3 4c.6 1.2 1.5 2.1 2.8 2.8l1.1-.8L8.8 7.6 7.7 9C4.3 8.6 1.4 5.7 1 2.3z" fill="#fff"/></svg>
        </span>
        <span>+1 410 555 0192</span>
      </li>
      <li class="contact__item">
        <span class="contact__icon">
          <svg viewBox="0 0 10 10"><rect x="1" y="2.2" width="8" height="5.6" fill="none" stroke="#fff" stroke-width="1"/><path d="M1 2.4 5 5.6 9 2.4" fill="none" stroke="#fff" stroke-width="1"/></svg>
        </span>
        <span>hello@beaconguard.com</span>
      </li>
      <li class="contact__item">
        <span class="contact__icon">
          <svg viewBox="0 0 10 10"><circle cx="5" cy="5" r="3.8" fill="none" stroke="#fff" stroke-width="1"/><path d="M1.2 5h7.6M5 1.2c-1.6 2.3-1.6 5.3 0 7.6M5 1.2c1.6 2.3 1.6 5.3 0 7.6" fill="none" stroke="#fff" stroke-width=".8"/></svg>
        </span>
        <span>www.beaconguard.com</span>
      </li>
    </ul>
  </div>
</section>

<section class="card card--back" aria-label="Business card back">
  <div class="brand">
    <span class="brand__square"></span>
    <span class="brand__name">BEACON GUARD LLC</span>
  </div>
</section>

</body>
</html>
```